Business Card Design needed for start up company Halvora

In need of a new business card designed for a start up company based in Sydney, Halvora is a new start up innovative Company, our mission it to make property accessible for everyday Australian and to become the leading Real Estate platform in Australia. We want it to be fresh and clean.

Industry/Entity Type

Financial

Contact Information for Business Card

Section for Name
Section for Title

HALVORA - The Strength of Pooling
Mobile:
Direct:

Font styles to use
Sans Serif

Colors
33a6d7
0692cd
0255a3
ffffff

Requirements
Must have
• Logo, all business card details

```html
<!DOCTYPE html>
<html lang="en">
<head>
<meta charset="utf-8">
<title>Halvora Business Card</title>
<link rel="stylesheet" href="https://fonts.googleapis.com/css2?family=Open+Sans:wght@400;600;700;800&display=swap">
<style>
  :root {
    --sky: #33a6d7;
    --azure: #0692cd;
    --navy: #0255a3;
    --ink-navy: #1d3a78;
    --white: #ffffff;
    --paper: #f7f8f9;
    --text-dark: #222a33;
    --backdrop: #2c2e32;
  }
  * { margin: 0; padding: 0; box-sizing: border-box; }
  html, body {
    width: 1200px;
    height: 864px;
    overflow: hidden;
    background: var(--backdrop);
    font-family: "Open Sans", Arial, sans-serif;
  }
  .stage {
    position: relative;
    width: 1200px;
    height: 864px;
  }
  .card {
    position: absolute;
    width: 600px;
    height: 340px;
    border-radius: 4px;
    overflow: hidden;
    box-shadow: 0 10px 30px rgba(0,0,0,0.45);
  }

  /* Front */
  .card-front {
    left: 250px;
    top: 62px;
    background: linear-gradient(180deg, #2a9cd9 0%, #1f6cb5 55%, #1d4a90 100%);
    color: var(--white);
    text-align: center;
  }
  .tagline {
    position: absolute;
    left: 0; right: 0; top: 10px;
    line-height: 1;
  }
  .tagline-lead {
    display: block;
    font-size: 150px;
    font-weight: 600;
    letter-spacing: 2px;
  }
  .tagline-rest {
    display: block;
    font-size: 50px;
    font-weight: 600;
    letter-spacing: 1.5px;
    margin-top: 12px;
  }
  .tagline-rest + .tagline-rest { margin-top: 6px; }

  /* Back */
  .card-back {
    left: 350px;
    top: 462px;
    background: var(--paper);
    color: var(--text-dark);
  }
  .brand {
    position: absolute;
    right: 48px;
    top: 52px;
    display: flex;
    align-items: center;
    gap: 10px;
    white-space: nowrap;
  }
  .brand-dot {
    width: 58px;
    height: 58px;
    border-radius: 50%;
    background: var(--sky);
    flex: none;
  }
  .brand-name {
    font-size: 44px;
    line-height: 1;
    font-weight: 800;
    color: var(--ink-navy);
  }
  .person {
    position: absolute;
    left: 40px;
    top: 148px;
  }
  .person-name {
    font-size: 19px;
    font-weight: 700;
    color: var(--ink-navy);
  }
  .person-name .given { color: var(--azure); }
  .person-title {
    font-size: 13px;
    color: var(--text-dark);
  }
  .divider {
    position: absolute;
    left: 0; right: 0;
    top: 196px;
    height: 1.5px;
    background: var(--azure);
  }
  .contacts {
    position: absolute;
    right: 34px;
    top: 232px;
    list-style: none;
    text-align: right;
  }
  .contacts li {
    display: flex;
    justify-content: flex-end;
    align-items: center;
    gap: 10px;
    font-size: 15px;
    line-height: 26px;
    color: var(--text-dark);
  }
  .contacts svg {
    width: 13px;
    height: 13px;
    flex: none;
  }
</style>
</head>
<body>
<main class="stage">
  <section class="card card-front" aria-label="Card front">
    <h1 class="tagline">
      <span class="tagline-lead">THE</span>
      <span class="tagline-rest">STRENGTH OF</span>
      <span class="tagline-rest">POOLING</span>
    </h1>
  </section>

  <section class="card card-back" aria-label="Card back">
    <div class="brand">
      <span class="brand-dot" aria-hidden="true"></span>
      <span class="brand-name">HALVORA</span>
    </div>

    <div class="person">
      <p class="person-name"><span class="given">Daniel</span> Reyes</p>
      <p class="person-title">Managing Director</p>
    </div>

    <div class="divider"></div>

    <ul class="contacts">
      <li>(044)-555-0182
        <svg viewBox="0 0 16 16" aria-hidden="true"><path fill="#0692cd" d="M3.6 1.5l2.3 2.4-1.3 1.9c.9 2 2.5 3.6 4.6 4.6l1.9-1.3 2.4 2.3-1.4 2.1C7 13.2 2.8 9 1.5 2.9z"/></svg>
      </li>
      <li>123-555-0147
        <svg viewBox="0 0 16 16" aria-hidden="true"><rect x="2.5" y="2.5" width="11" height="11" rx="2" fill="none" stroke="#0692cd" stroke-width="2"/></svg>
      </li>
      <li>info@halvora.com
        <svg viewBox="0 0 16 16" aria-hidden="true"><rect x="1" y="3.5" width="14" height="9" fill="#0692cd"/><path d="M1.5 4l6.5 5 6.5-5" fill="none" stroke="#ffffff" stroke-width="1.2"/></svg>
      </li>
    </ul>
  </section>
</main>
</body>
</html>
```